Website for software company "velora"

We need a website for our software company/startup named "velora". We are developing several products (currently 3 standard-software products) which are all in different sectors, but all our products are available for Laptops/PC/Mobile Phones/Tablets, ... We do also create custom software and support our customers with consulting to optimize their processes.
We already have a Logo which you can find in the attached files.
We are a young team of 4 members (two founders and 2 employees).

To get an idea of our products -> the first one is a planning software for healthcare organizations (eg. BlueHaven, firebrigade, pharmacy), the second one is a booking software for sport clubs and the third one is a competition software for sports hunting. You see very diverse. Include or ignore this info of our products as you like.

The design has to be a bootstrap 4 (or higher) design. We have licenced FontAwesome as iconset. Responsive design should come without saying.

• Starting page, product pages, news section, contact, team, services

```html
<!DOCTYPE html>
<html lang="en">
<head>
<meta charset="utf-8">
<title>Velora Software</title>
<link rel="stylesheet" href="https://fonts.googleapis.com/css2?family=Josefin+Sans:wght@400;600;700&family=Lato:wght@400;700&display=swap">
<style>
:root{
  --orange:#f58634;
  --orange-deep:#ec7a27;
  --ink:#1b1b1b;
  --text:#333;
  --muted:#8a8a8a;
  --soft:#f4f4f4;
  --white:#fff;
  --black:#000;
}
*{box-sizing:border-box;margin:0;padding:0}
html,body{width:1200px;height:3881px;overflow:hidden}
body{position:relative;background:var(--white);font-family:"Lato",sans-serif;color:var(--text)}
.abs{position:absolute}
h1,h2,h3,h4,.brand,.btn,.link-more{font-family:"Josefin Sans",sans-serif}
.btn{display:inline-flex;align-items:center;justify-content:center;font-weight:700;font-size:16px;color:var(--white);background:var(--orange);position:absolute;text-decoration:none}
.btn::after{content:"";position:absolute;top:6px;right:6px;width:6px;height:6px;border-top:1.5px solid #fff;border-right:1.5px solid #fff}
.brand{display:flex;align-items:center;gap:10px;font-weight:700;letter-spacing:2px}
.brand .mark{width:30px;height:30px;background:var(--orange)}
.eyebrow{font-family:"Lato",sans-serif;color:var(--orange);font-size:15px;font-weight:700;display:flex;align-items:center;gap:10px}
.eyebrow::before,.eyebrow.center::after{content:"";width:28px;height:2px;background:var(--orange)}
.section-title{font-size:36px;font-weight:600;color:var(--ink);text-align:center}
.link-more{color:var(--orange);font-size:15px;font-weight:700}

/* hero */
.hero{left:0;top:0;width:1200px;height:780px;overflow:hidden}
.hero-photo{position:absolute;inset:0;background:linear-gradient(100deg,#3b3836 0%,#5b5650 35%,#8a7a66 60%,#6b5a4a 100%)}
.hero-shade{position:absolute;inset:0;background:linear-gradient(90deg,rgba(0,0,0,.45),rgba(0,0,0,.05))}
.nav{left:112px;top:26px;width:976px;height:73px;background:var(--white);display:flex;align-items:center;padding:0 22px}
.nav .brand{font-size:40px;color:var(--ink)}
.nav ul{list-style:none;display:flex;gap:36px;margin-left:auto;margin-right:44px;font-size:15px;color:var(--ink)}
.nav li.active{color:var(--orange)}
.nav .login{position:relative;background:var(--orange);color:#fff;font-family:"Josefin Sans",sans-serif;font-weight:700;font-size:16px;width:94px;height:45px;display:flex;align-items:center;justify-content:center}
.nav .login::after{content:"";position:absolute;top:6px;right:6px;width:6px;height:6px;border-top:1.5px solid #fff;border-right:1.5px solid #fff}
.hero h1{left:112px;top:212px;font-size:62px;line-height:68px;color:var(--white);font-weight:700}
.hero .lead{left:112px;top:438px;color:var(--white);font-size:14px;font-weight:700;border-left:3px solid var(--orange);padding-left:8px}
.hero .btn-start{left:112px;top:491px;width:138px;height:48px}
.hero .btn-learn{left:266px;top:491px;width:138px;height:48px;background:transparent;border:1.5px solid #fff}
.hero svg{position:absolute;left:0;bottom:0}

/* about */
.about-img{left:110px;top:864px;width:455px;height:350px;background:linear-gradient(135deg,#f6b27e,#e98a45 55%,#b06a3c);box-shadow:0 8px 16px rgba(0,0,0,.15)}
.about .eyebrow{left:598px;top:834px}
.about h2{left:598px;top:866px;width:420px;font-size:34px;line-height:44px;font-weight:600;color:var(--ink)}
.about p{left:598px;top:964px;width:492px;font-size:14.5px;line-height:25.6px;color:var(--muted);text-align:justify}
.about .btn{left:599px;top:1192px;width:138px;height:48px}

/* software */
.software{left:0;top:1311px;width:1200px;height:631px;background:var(--soft)}
.software .eyebrow{left:533px;top:66px}
.software h2{left:0;top:98px;width:1200px}
.card{position:absolute;top:227px;width:281px;height:319px;background:#fff;border-radius:8px;box-shadow:0 2px 10px rgba(0,0,0,.06);text-align:center}
.card .icon{position:absolute;left:78px;top:-56px;width:124px;height:124px;border-radius:50%;background:var(--orange);display:flex;align-items:center;justify-content:center}
.card h3{position:absolute;top:87px;width:100%;font-size:27px;font-weight:600;color:var(--ink)}
.card p{position:absolute;top:129px;left:20px;right:20px;font-size:14.5px;line-height:25.6px;color:var(--muted)}
.card .link-more{position:absolute;top:279px;width:100%;left:0}

/* blog */
.blog{left:0;top:1942px;width:1200px;height:738px;background:linear-gradient(120deg,#f2873b,#f08036 50%,#ee7f35)}
.blog h2{left:0;top:66px;width:1200px;color:#fff}
.post{position:absolute;background:#fff;padding:11px}
.post .ph{background:linear-gradient(135deg,#7d8fa6,#3d4a5c 60%,#b9c2cc)}
.post h3{font-size:25px;font-weight:600;color:var(--ink);line-height:30px}
.post .date{font-size:14.5px;color:var(--muted);display:flex;align-items:center;gap:8px;margin-top:10px}
.post .date i{width:13px;height:13px;border:2px solid var(--orange);border-radius:2px;display:inline-block}
.post p{font-size:14.5px;line-height:25.6px;color:var(--text);margin-top:8px}
.post .link-more{display:block;margin-top:6px}
.post.big{left:110px;top:146px;width:482px;height:515px}
.post.big .ph{height:316px}
.post.big .body{padding:16px 5px 0}
.post.big p{width:420px}
.post.small{left:618px;width:470px;height:249px;display:flex;gap:20px}
.post.small .ph{width:224px;height:227px;flex:none}
.post.small .body{padding-top:12px}

/* contact */
.contact{left:0;top:2680px;width:1200px;height:760px;background:var(--soft)}
.contact .eyebrow{left:533px;top:78px}
.contact h2{left:0;top:108px;width:1200px}
.info{position:absolute;left:174px;display:flex;gap:12px}
.info .dot{width:52px;height:52px;border-radius:50%;background:#fff;box-shadow:0 2px 8px rgba(0,0,0,.06);display:flex;align-items:center;justify-content:center;flex:none}
.info h4{font-family:"Lato",sans-serif;font-size:15px;font-weight:700;color:var(--ink);margin-top:2px}
.info p{font-size:15px;line-height:23px;color:var(--ink);margin-top:4px;width:300px}
.info a{color:var(--orange);text-decoration:none}
.form{position:absolute;left:585px;top:187px;width:439px;height:442px;background:#fff;padding:40px 46px}
.form h3{font-size:28px;font-weight:600;color:var(--ink)}
.field{border-bottom:1.5px solid #444;font-size:15px;color:var(--ink);padding-bottom:10px;margin-top:34px}
.field:first-of-type{margin-top:28px}
.form .send{position:absolute;left:46px;top:358px;width:112px;height:44px;border-radius:22px;background:var(--orange);color:#fff;font-family:"Josefin Sans",sans-serif;font-weight:700;font-size:17px;display:flex;align-items:center;justify-content:center}

/* footer */
.footer{left:0;top:3378px;width:1200px;height:503px;background:var(--soft)}
.footer svg{position:absolute;left:0;top:0}
.footer .base{position:absolute;left:0;top:134px;width:1200px;height:369px;background:var(--black)}
.footer .brand{position:absolute;left:112px;top:194px;font-size:60px;color:#fff}
.footer .brand .mark{width:48px;height:48px}
.socials{position:absolute;left:208px;top:305px;display:flex;gap:12px}
.socials span{width:13px;height:13px;border-radius:50%;background:var(--orange)}
.fcol{position:absolute;top:192px;color:#fff}
.fcol h4{font-family:"Lato",sans-serif;font-size:19px;font-weight:400;margin-bottom:18px}
.fcol ul{list-style:none;font-size:15px;line-height:30px;padding-left:3px}
.newsletter input{all:unset;display:block;width:243px;border-bottom:1px solid #555;border-left:2px solid #fff;padding:2px 12px 8px;font-size:14px;color:#666;margin-top:-2px}
.newsletter .sub{margin-top:28px;width:120px;height:36px;border-radius:18px;background:var(--orange);box-shadow:0 0 14px rgba(245,134,52,.7);color:#fff;font-family:"Josefin Sans",sans-serif;font-weight:700;font-size:15px;display:flex;align-items:center;justify-content:center}
.footer .rule{position:absolute;left:112px;top:415px;width:976px;height:1px;background:#2b2b2b}
.footer .copy{position:absolute;left:0;top:446px;width:1200px;text-align:center;color:#fff;font-size:15px}
</style>
</head>
<body>

<header class="hero abs">
  <div class="hero-photo" role="img" aria-label="Photo of a team walking through a bright modern office"></div>
  <div class="hero-shade"></div>
  <nav class="nav abs">
    <div class="brand"><span class="mark"></span>VELORA</div>
    <ul><li class="active">Home</li><li>Our Software</li><li>Our Blog</li><li>About Us</li><li>Contact Us</li></ul>
    <div class="login">Login</div>
  </nav>
  <h1 class="abs">Welcome To<br>Velora Software<br>Company</h1>
  <p class="lead abs">Lorem ipsum dolor sit amet, consectetur adipiscing elit, sed</p>
  <a class="btn btn-start">Get Started</a>
  <a class="btn btn-learn">Learn More</a>
  <svg width="1200" height="200" viewBox="0 0 1200 200">
    <polygon points="120,102 603,184 1200,64 1200,30" fill="#f58634"/>
    <polygon points="0,61 603,164 1200,56 1200,200 0,200" fill="#fff"/>
  </svg>
</header>

<section class="about">
  <div class="about-img abs" role="img" aria-label="Photo of a smiling woman with glasses at work, orange toned"></div>
  <div class="eyebrow abs">About Us</div>
  <h2 class="abs">About Velora Software Company</h2>
  <p class="abs">Lorem ipsum dolor sit amet, consectetur adipiscing elit, sed do eiusmod tempor incididunt ut labore et dolore magna aliqua. Quis ipsum suspendisse ultrices gravida. Risus commodo viverra maecenas accumsan lacus vel facilisis. Lorem ipsum dolor sit amet, consectetur adipiscing elit, sed do eiusmod tempor incididunt ut labore et dolore magna aliqua. Quis ipsum suspendisse ultrices gravida. Risus commodo viverra maecenas accumsan lacus vel facilisis. Lorem ipsum dolor sit amet, consectetur adipiscing elit, sed do eiusmod</p>
  <a class="btn">Learn More</a>
</section>

<section class="software abs">
  <div class="eyebrow center abs">Software</div>
  <h2 class="section-title abs">Our Software</h2>
  <div class="card" style="left:158px">
    <div class="icon"><svg width="64" height="64" viewBox="0 0 64 64" fill="none" stroke="#fff" stroke-width="2.5" stroke-linejoin="round"><path d="M32 30 C20 22 18 12 25 9 C29 7 32 11 32 13 C32 11 35 7 39 9 C46 12 44 22 32 30Z"/><path d="M29 17h6M32 14v6"/><path d="M6 30 L14 44 L22 52 L28 52 L28 44 L20 36"/><path d="M58 30 L50 44 L42 52 L36 52 L36 44 L44 36"/></svg></div>
    <h3>Healthcare</h3>
    <p>Lorem ipsum dolor sit amet, consectetur adipiscing elit, sed do eiusmod tempor incididunt ut labore et dolore magna aliqua. Quis ipsum suspendisse ultrices</p>
    <span class="link-more">Learn More</span>
  </div>
  <div class="card" style="left:460px">
    <div class="icon"><svg width="70" height="64" viewBox="0 0 70 64" fill="none" stroke="#fff" stroke-width="2.5" stroke-linejoin="round"><circle cx="35" cy="10" r="6"/><path d="M20 28 L35 18 L50 28"/><path d="M8 30h54v26H8z"/><path d="M30 56V44h10v12M14 38h8v6h-8zM48 38h8v6h-8z"/></svg></div>
    <h3>Sport Clubs</h3>
    <p>Lorem ipsum dolor sit amet, consectetur adipiscing elit, sed do eiusmod tempor incididunt ut labore et dolore magna aliqua. Quis ipsum suspendisse ultrices</p>
    <span class="link-more">Learn More</span>
  </div>
  <div class="card" style="left:761px">
    <div class="icon"><svg width="84" height="84" viewBox="0 0 84 84" fill="none" stroke="#fff" stroke-width="2.5"><circle cx="42" cy="42" r="38"/><circle cx="42" cy="42" r="26"/><circle cx="42" cy="42" r="14"/><circle cx="42" cy="42" r="4" fill="#fff"/><path d="M42 10v18M42 56v18M10 42h18M56 42h18"/></svg></div>
    <h3>Sports Hunting</h3>
    <p>Lorem ipsum dolor sit amet, consectetur adipiscing elit, sed do eiusmod tempor incididunt ut labore et dolore magna aliqua. Quis ipsum suspendisse ultrices</p>
    <span class="link-more">Learn More</span>
  </div>
</section>

<section class="blog abs">
  <h2 class="section-title abs">Our Latest Blog</h2>
  <article class="post big">
    <div class="ph" role="img" aria-label="Photo of two colleagues looking at a laptop in an office"></div>
    <div class="body">
      <h3>Lorem ipsum dolor sit</h3>
      <div class="date"><i></i>April 16 2022</div>
      <p>Lorem ipsum dolor sit amet, consectetur adipiscing elit, sed do eiusmod tempor incididunt ut labore et dolore</p>
      <span class="link-more">Learn More</span>
    </div>
  </article>
  <article class="post small" style="top:146px">
    <div class="ph" role="img" aria-label="Photo of a man working on a laptop at a desk"></div>
    <div class="body">
      <h3>Lorem ipsum<br>dolor sit</h3>
      <div class="date"><i></i>April 16 2022</div>
      <p>Lorem ipsum dolor sit amet, consectetur adipiscing elit, sed do eiusmod tempor</p>
      <span class="link-more">Learn More</span>
    </div>
  </article>
  <article class="post small" style="top:414px">
    <div class="ph" role="img" aria-label="Photo of a man typing on a laptop in a library"></div>
    <div class="body">
      <h3>Lorem ipsum<br>dolor sit</h3>
      <div class="date"><i></i>April 16 2022</div>
      <p>Lorem ipsum dolor sit amet, consectetur adipiscing elit, sed do eiusmod tempor</p>
      <span class="link-more">Learn More</span>
    </div>
  </article>
</section>

<section class="contact abs">
  <div class="eyebrow center abs">Contact</div>
  <h2 class="section-title abs">Contact Us</h2>
  <div class="info" style="top:277px">
    <span class="dot"><svg width="14" height="18" viewBox="0 0 14 18"><path d="M7 0a7 7 0 0 1 7 7c0 5-7 11-7 11S0 12 0 7a7 7 0 0 1 7-7z" fill="#f58634"/><circle cx="7" cy="7" r="2.5" fill="#fff"/></svg></span>
    <div><h4>Address</h4><p>Lorem ipsum dolor sit amet, consectetur adipiscing elit</p></div>
  </div>
  <div class="info" style="top:388px">
    <span class="dot"><svg width="16" height="16" viewBox="0 0 16 16"><path d="M3 1l3 3-2 2c1 2 3 4 5 5l2-2 3 3-2 3C6 15 1 10 1 3z" fill="#f58634"/></svg></span>
    <div><h4>Phone</h4><p>+1 555 014 2290</p></div>
  </div>
  <div class="info" style="top:490px">
    <span class="dot"><svg width="16" height="12" viewBox="0 0 16 12"><rect width="16" height="12" rx="1.5" fill="#f58634"/><path d="M1 1l7 6 7-6" stroke="#fff" stroke-width="1.5" fill="none"/></svg></span>
    <div><h4>Email</h4><p><a>info@velorasoftware.com</a></p></div>
  </div>
  <div class="form">
    <h3>Send Message</h3>
    <div class="field">Full Name</div>
    <div class="field">Last Name</div>
    <div class="field">Address</div>
    <div class="field">Types Your Message</div>
    <div class="send">Send</div>
  </div>
</section>

<footer class="footer abs">
  <svg width="1200" height="140" viewBox="0 0 1200 140">
    <polygon points="0,134 603,0 1200,134" fill="#f58634"/>
    <polygon points="20,140 603,16 1180,140" fill="#000"/>
  </svg>
  <div class="base"></div>
  <div class="brand"><span class="mark"></span>VELORA</div>
  <div class="socials" aria-label="Social links"><span></span><span></span><span></span><span></span></div>
  <div class="fcol" style="left:489px"><h4>Quick Link</h4><ul><li>Home</li><li>Our Software</li><li>Our Blog</li><li>About Us</li><li>Contact Us</li></ul></div>
  <div class="fcol" style="left:643px"><h4>Support</h4><ul><li>Terms&amp;condtions</li><li>Privacy Policy</li><li>About Us</li><li>Support</li></ul></div>
  <div class="fcol newsletter" style="left:845px"><h4>Subscribe To Our Newsletter</h4><input placeholder="Enter Your Email" aria-label="Email"><div class="sub">Subscribe</div></div>
  <div class="rule"></div>
  <p class="copy">©Copyrights 2022 Velora &nbsp;|&nbsp; All Rights Reserved</p>
</footer>

</body>
</html>
```